Honey jar label for small US farm

My daughters have 6 beehives and will be producing 300-400 jars of honey this season that they plan to sell at the farmers' market.
We are looking for a label design for small honey jars.
Label size:  1.5 inches high and 3 inches wide.
The label will be a simple RECTANGLE (no special cut)
We would like a playful look but upscale enough. We don't think that flowers or bees add anything. We like cleaner looks but not cold.
Maybe one could also represent the 3 sisters somewhere on the label. As elegant stick figures maybe?
One could also imagine a design where the label is black and the text/images are white to add some dramatic effect. The jar lid is black.
The honey is raw, un-pasturized, straight from the beehive.

Target Market(s)
Farm stand, sold by the 3 sisters who are 11, 9 and 6
Industry/Entity Type
Food Production
Colors
Designer to choose colors to be used in the design.
Requirements
Must have
- Name (means three sisters in English): Clos Vert
- What it is: Berkshire Raw Honey
- Net weight: 3.75oz (110ml)
- Location: Alder Falls, MA
- Text on one of the sides: Sister to sister we will always be, a couple of nuts off the family tree!
- Note that the jar is an hexagon. See the attached STOCK photo.
- Therefore, a little more than 1 inch is on the front facing, and 0.75 inches on each sides.

Nice to have
- The design should be elegant (but not ornate), but clean. Inviting and fun.
- No need for bees or flowers which would not make it look upscale.
- No gold or "over the top" fancy. Modern but not cold.
- Remember that this is a honey brand for 3 young sisters. Something playful but upscale would work too.
- Not sure about color codes. We are quite happy staying in grey scales, but a little bit of colour might work too.

Should not have
- No UPC code needed

```html
<!DOCTYPE html>
<html lang="en">
<head>
<meta charset="utf-8">
<title>Clos Vert — Berkshire Raw Honey Label</title>
<link rel="stylesheet" href="https://fonts.googleapis.com/css2?family=Marcellus&family=Kaushan+Script&family=Tinos:wght@400;700&display=swap">
<style>
  :root {
    --page: #f4f4f4;
    --label-side: #2b2b2b;
    --label-front: #262626;
    --label-quote: #060606;
    --ink: #ffffff;
    --ink-soft: #d9d9d9;
    --ghost: #5e5e5e;
    --honey: #f2c21b;
  }
  * { box-sizing: border-box; margin: 0; padding: 0; }
  html, body { width: 1200px; height: 905px; overflow: hidden; }
  body {
    background: var(--page);
    display: flex;
    align-items: center;
    justify-content: center;
  }
  .label {
    width: 1020px;
    height: 510px;
    display: grid;
    grid-template-columns: 255px 510px 255px;
    box-shadow: 0 10px 30px rgba(0,0,0,0.18);
  }
  .panel { position: relative; height: 100%; }

  /* left side */
  .panel--side { background: var(--label-side); }
  .sisters-ghost {
    position: absolute;
    left: 32px; top: 120px;
    width: 150px; height: 250px;
    background: linear-gradient(180deg, #6a6a6a, var(--ghost));
    border-radius: 60px 60px 14px 14px;
    opacity: 0.75;
  }
  .location {
    position: absolute;
    right: 36px; top: 50%;
    transform: translate(50%, -50%) rotate(-90deg);
    font-family: "Tinos", serif;
    font-weight: 700;
    font-size: 15px;
    color: var(--ink);
    white-space: nowrap;
    letter-spacing: 0.02em;
  }

  /* front */
  .panel--front {
    background: var(--label-front);
    display: flex;
    flex-direction: column;
    align-items: center;
    color: var(--ink);
  }
  .sisters-figure {
    margin-top: 86px;
    width: 130px; height: 108px;
    background: linear-gradient(180deg, #ffffff, #e6e6e6);
    border-radius: 50px 50px 10px 10px;
  }
  .brand-name {
    margin-top: 20px;
    font-family: "Marcellus", serif;
    font-size: 62px;
    line-height: 1;
    letter-spacing: 0.02em;
    color: var(--ink);
  }
  .product {
    margin-top: 14px;
    font-family: "Kaushan Script", cursive;
    font-size: 22px;
    color: var(--honey);
  }
  .net-weight {
    margin-top: auto;
    margin-bottom: 58px;
    text-align: center;
    font-family: "Tinos", serif;
    font-weight: 700;
    font-size: 19px;
    line-height: 1.35;
  }
  .net-weight__title {
    display: inline-block;
    padding: 0 10px 2px;
    border-bottom: 1.5px solid var(--ink);
  }

  /* right side */
  .panel--quote {
    background: var(--label-quote);
    display: flex;
    flex-direction: column;
    align-items: center;
    justify-content: center;
    gap: 34px;
    color: var(--ink);
  }
  .comb-mark {
    width: 40px; height: 46px;
    background: #3a3a3a;
    border-radius: 6px;
  }
  .motto {
    font-family: "Kaushan Script", cursive;
    font-size: 21px;
    line-height: 1.75;
    text-align: center;
  }
</style>
</head>
<body>
  <main class="label">
    <section class="panel panel--side">
      <div class="sisters-ghost" role="img" aria-label="Faint grey silhouettes of three sisters"></div>
      <p class="location">Location: Alder Falls, MA</p>
    </section>

    <section class="panel panel--front">
      <div class="sisters-figure" role="img" aria-label="White silhouettes of three young sisters"></div>
      <h1 class="brand-name">Clos Vert</h1>
      <p class="product">Berkshire Raw Honey</p>
      <p class="net-weight">
        <span class="net-weight__title">Net weight</span><br>
        3.75oz /110ml
      </p>
    </section>

    <section class="panel panel--quote">
      <div class="comb-mark" role="img" aria-label="Small honeycomb outline motif"></div>
      <p class="motto">Sister to sister<br>we will always be,<br>a couple of nuts off<br>the family tree</p>
      <div class="comb-mark" role="img" aria-label="Small honeycomb outline motif"></div>
    </section>
  </main>
</body>
</html>
```